At Home Pet Euthanasia - business cards & brand stationary

We already have a logo and the colors and a website. Need a business card designed that will be able to customized to multiple veterinarians who will be partnering with us. The feel needs to be compassionate, comforting with our tagline 'A Gift of Love at Home'. It will be 2 sides.
On the back our platform/partner vets will be customizing each business card with their own service areas, phone numbers, name and title. On the front, i would like to see experimentation with use of our photos, the logo, tagline and a description 'Peaceful and Compassionate At-Home Pet Euthanasia'

```html
<!DOCTYPE html>
<html lang="en">
<head>
<meta charset="utf-8">
<title>Stillwater Pet – Business Card</title>
<link rel="stylesheet" href="https://fonts.googleapis.com/css2?family=Dancing+Script:wght@600&family=Mulish:ital,wght@0,300;0,400;0,700;1,300&display=swap">
<style>
  :root {
    --backdrop: #1c1c1e;
    --brand-blue: #7b9cc8;
    --band-blue: #7f9dc9;
    --paw-light: #c3dcf7;
    --paw-mid: #6d8fd0;
    --paw-deep: #1f4fa6;
    --white: #ffffff;
    --photo-warm: #e9b9a6;
    --photo-grey: #d9d8d6;
    --photo-cool: #a9b2b4;
  }
  * { box-sizing: border-box; margin: 0; padding: 0; }
  html, body {
    width: 1200px; height: 800px; overflow: hidden;
    background: var(--backdrop);
  }
  .canvas {
    width: 1200px; height: 800px;
    display: flex; flex-direction: column; align-items: center; justify-content: center;
    gap: 36px;
  }
  .card {
    position: relative;
    width: 600px; height: 343px;
    overflow: hidden;
    box-shadow: 0 10px 28px rgba(0,0,0,.55);
  }

  /* Front */
  .card-front .photo-area {
    position: absolute; inset: 0;
    background:
      radial-gradient(ellipse 30% 45% at 62% 38%, #ece7e1 0%, transparent 70%),
      radial-gradient(ellipse 35% 40% at 28% 82%, var(--photo-warm) 0%, transparent 75%),
      linear-gradient(100deg, var(--photo-cool) 0%, #c9c2bb 30%, var(--photo-grey) 60%, #e4e3e1 100%);
  }
  .card-front .tagline-band {
    position: absolute; left: 0; right: 0; top: 248px; height: 46px;
    background: var(--band-blue);
    display: flex; align-items: center; justify-content: center;
  }
  .card-front .description {
    font-family: "Dancing Script", cursive;
    font-weight: 600; font-size: 27px; color: var(--white);
    letter-spacing: .3px;
  }

  /* Back */
  .card-back { background: var(--brand-blue); color: var(--white); font-family: "Mulish", sans-serif; }
  .brand {
    position: absolute; left: 48px; top: 58px;
  }
  .brand-row { display: flex; align-items: center; gap: 12px; }
  .brand-mark { width: 40px; height: 40px; background: var(--white); border-radius: 50%; }
  .brand-name { font-weight: 700; font-size: 40px; line-height: 1; letter-spacing: -.5px; }
  .brand-tagline {
    margin: 8px 0 0 70px;
    font-style: italic; font-weight: 300; font-size: 15px;
  }
  .contact { position: absolute; left: 78px; top: 170px; }
  .person-name { font-weight: 700; font-size: 19px; letter-spacing: .6px; text-transform: uppercase; }
  .person-title { font-weight: 400; font-size: 14px; margin-top: 1px; }
  .address { font-size: 13.5px; line-height: 1.3; margin-top: 18px; }
  .links { list-style: none; margin-top: 14px; font-size: 13.5px; line-height: 1.35; }
  .links li { display: flex; align-items: center; gap: 8px; }
  .links svg { width: 11px; height: 11px; fill: var(--white); flex: none; }
  .paw-pattern {
    position: absolute; right: 0; top: 0; bottom: 0; width: 270px;
    background: linear-gradient(135deg, var(--paw-light) 0%, var(--paw-mid) 55%, var(--paw-deep) 100%);
    opacity: .55;
  }
</style>
</head>
<body>
<main class="canvas">

  <section class="card card-front">
    <div class="photo-area" role="img" aria-label="Photograph of a child hugging a blue-eyed cat"></div>
    <div class="tagline-band">
      <p class="description">Peaceful &amp; Compassionate At-Home Pet Euthanasia</p>
    </div>
  </section>

  <section class="card card-back">
    <div class="brand">
      <div class="brand-row">
        <span class="brand-mark"></span>
        <span class="brand-name">Stillwater Pet</span>
      </div>
      <p class="brand-tagline">A gift of love at home.</p>
    </div>

    <div class="contact">
      <h1 class="person-name">Daniel Reyes</h1>
      <p class="person-title">President</p>
      <p class="address">412 Willow Bend Road<br>Juneau, Alaska 99801</p>
      <ul class="links">
        <li><svg viewBox="0 0 24 24"><path d="M6.6 10.8a15 15 0 0 0 6.6 6.6l2.2-2.2a1 1 0 0 1 1-.25 11.4 11.4 0 0 0 3.6.57 1 1 0 0 1 1 1V20a1 1 0 0 1-1 1A17 17 0 0 1 3 4a1 1 0 0 1 1-1h3.5a1 1 0 0 1 1 1c0 1.25.2 2.45.57 3.57a1 1 0 0 1-.25 1z"/></svg>555-014-2273</li>
        <li><svg viewBox="0 0 24 24"><path d="M2 5h20v14H2z M2 5l10 8 10-8" stroke="#7b9cc8" stroke-width="1.5"/></svg>daniel@stillwaterpet.com</li>
        <li><svg viewBox="0 0 24 24"><circle cx="12" cy="12" r="10"/><path d="M2 12h20M12 2c3 3 3 17 0 20M12 2c-3 3-3 17 0 20" fill="none" stroke="#7b9cc8" stroke-width="1.5"/></svg>www.stillwaterpet.com</li>
      </ul>
    </div>

    <div class="paw-pattern" role="img" aria-label="Decorative pattern of heart-shaped paw prints in shades of blue"></div>
  </section>

</main>
</body>
</html>
```